Cat-products company needs smart, yet endearing, business card

We need a business card design for a new, but up-and-running, business based in Honolulu, Hawaii. The business is Purrnest Nook Co. Our first product is the most environmentally-friendly cat grass kit ever seen on the planet. Future products, currently in the R&D phase, will include a variety of exciting cat scratchers. We also do consulting work to help apartment-dwellers make their home more cat-friendly and, in the future, plan on doing full, custom installs of structure to create high walkways for cats.

Target Market(s)

Middle-aged, apartment-dwelling, middle-class workers who own 1 or more cats and who dote on them.

Industry/Entity Type

Pet Care

Contact Information for Business Card

A striking, professional, yet warm and friendly design is what we're after.

Font styles to use
Serif
Sans Serif
Other font styles liked:
• Comfortaa

Colors

Designer to choose colors to be used in the design.

Requirements
Must have
• The company logo: (see attachment)
• The company name: Purrnest Nook Co
• The web address: www.purrnestnookco.com
• Email: support@purrnestnookco.com
• Phone: +1 (808) 571 6023
• Update (Fri Jun 30 3017 7:45pm Hawaii Time) I would like, is possible, uploaded picture of the cat grass kit on the back of the card with some text along the lines of: Purrnest Nook Co - Maker Of The Leafiest Feline Sprout Set Yet
Nice to have
• A cat picture, cartoon, real or silhouette that illustrates cats in action and/or relaxing; ie using the apartment space to live, play and relax in and being well-contented.
• Most of the website is done in the font: Comfortaa. It might be nice to continue using this for brand consistency.
Should not have
• Hard-to-read fonts.

```html
<!DOCTYPE html>
<html lang="en">
<head>
<meta charset="utf-8">
<title>Purrnest Nook Co – Business Card</title>
<link rel="stylesheet" href="https://fonts.googleapis.com/css2?family=Jost:wght@400;600&display=swap">
<style>
  :root {
    --stage: #2b2b2b;
    --sun: #f0ad00;
    --cocoa: #553028;
    --ink: #4a2b22;
    --paper: #f2f2f2;
  }
  * { box-sizing: border-box; margin: 0; padding: 0; }
  html, body { width: 1200px; height: 960px; overflow: hidden; }
  body {
    background: var(--stage);
    font-family: "Jost", "Helvetica Neue", Arial, sans-serif;
    color: var(--ink);
    position: relative;
  }
  .card {
    position: absolute;
    width: 600px;
    height: 342px;
    border-radius: 22px;
    overflow: hidden;
  }
  .card-front { left: 314px; top: 114px; background: var(--sun); }
  .card-back  { left: 311px; top: 473px; background: var(--paper); }

  .holder { position: absolute; left: 37px; top: 48px; }
  .holder-name { font-weight: 600; font-size: 22px; letter-spacing: 0.2px; text-transform: uppercase; line-height: 1.1; }
  .holder-role { font-size: 15px; text-transform: uppercase; margin-top: 4px; margin-left: -2px; }

  .contact { position: absolute; left: 37px; top: 163px; font-size: 15px; line-height: 19px; }
  .contact .address { margin-bottom: 9px; }
  .contact .label { font-weight: 600; }

  .social { position: absolute; left: 37px; top: 281px; display: flex; gap: 3px; }
  .social span { width: 29px; height: 29px; border-radius: 50%; background: var(--cocoa); display: block; }

  .front-mark {
    position: absolute; left: 300px; top: 0; width: 300px; height: 342px;
    display: flex; flex-direction: column; align-items: center; justify-content: center; gap: 22px;
  }
  .front-square { width: 170px; height: 170px; background: var(--cocoa); }
  .front-name { font-weight: 600; font-size: 28px; color: var(--cocoa); line-height: 1; }

  .brand {
    position: absolute; left: 0; right: 0; top: 62px;
    display: flex; flex-direction: column; align-items: center;
  }
  .brand-square { width: 120px; height: 120px; background: var(--cocoa); }
  .brand-name { margin-top: 24px; font-weight: 600; font-size: 46px; color: var(--sun); line-height: 1; }
</style>
</head>
<body>
  <section class="card card-front">
    <div class="holder">
      <p class="holder-name">Leilani Hart</p>
      <p class="holder-role">CEO/Founder</p>
    </div>
    <div class="contact">
      <p class="address">2140 Plumeria Way<br>Honolulu, Hawaii 96815</p>
      <p><span class="label">P:</span> +1 (808) 571 6023</p>
      <p>support@purrnestnookco.com</p>
      <p>www.purrnestnookco.com</p>
    </div>
    <div class="social" aria-label="Social links">
      <span></span><span></span><span></span><span></span>
    </div>
    <div class="front-mark">
      <div class="front-square"></div>
      <p class="front-name">Purrnest Nook Co</p>
    </div>
  </section>

  <section class="card card-back">
    <div class="brand">
      <div class="brand-square"></div>
      <p class="brand-name">Purrnest Nook Co</p>
    </div>
  </section>
</body>
</html>
```